Board Presentation template

Design a simple and clean PowerPoint slide templates for a Board meeting. The slides should have predominantly white backgrounds and use the colors of our Logo (attached): Tones of grey and orange and blue.
The company name is called Keystone Lane Gauging.
It sell, calibrate, service and repair industrial and commercial scales of all types. In particular, Truck scales, floor scales, counting scales and benchtop scales.
There is no website for Keystone Lane Gauging, but we have three affiliates that have their own websites:
https://www.fernwaybalance.example/
https://meadowlarkhandlingandmassing.example/
https://tvbalance.example/
Target Market(s)
Industrial and Commercial Weighing systems
Industry/Entity Type
Look and feel

```html
<!DOCTYPE html>
<html lang="en">
<head>
<meta charset="utf-8">
<title>Keystone Lane Gauging – Board Presentation Slides</title>
<link rel="stylesheet" href="https://fonts.googleapis.com/css2?family=Bebas+Neue&family=Montserrat:ital,wght@0,300;0,400;0,500;1,400&display=swap">
<style>
:root{
  --page:#f2f2f2;
  --white:#ffffff;
  --slate:#3d4a54;
  --slate-band:#455561;
  --blue:#2e6a97;
  --blue-dark:#24577d;
  --red:#e2493b;
  --text:#4a4f55;
  --muted:#a9a9a9;
  --rule:#6b7680;
}
*{margin:0;padding:0;box-sizing:border-box}
html,body{width:1200px;height:2710px;overflow:hidden}
body{background:var(--page);font-family:"Montserrat",sans-serif;color:var(--text);position:relative}
.option-title{position:absolute;left:0;width:1200px;text-align:center;font-size:50px;font-weight:400;color:var(--slate);line-height:64px}
.slide{position:absolute;left:129px;width:941px;height:529px;background:var(--white);box-shadow:8px 14px 22px rgba(0,0,0,.18);overflow:hidden}
.date{position:absolute;left:746px;top:6px;display:flex;align-items:center;gap:9px;font-size:11.5px;color:var(--muted)}
.date svg{width:21px;height:18px}
.footer-band{position:absolute;left:0;top:499px;width:941px;height:21px;background:var(--blue);color:var(--white);font-size:11px;line-height:21px}
.slide.slate-footer .footer-band{background:var(--slate-band)}
.slide.mixed-footer .footer-band{background:linear-gradient(90deg,var(--blue),var(--slate-band))}
.footer-band .copyright{position:absolute;left:289px;top:0}
.footer-band .page-label{position:absolute;left:863px;top:0}
.footer-band .page-num{position:absolute;left:905px;top:0;width:36px;text-align:center;border-left:1px solid rgba(255,255,255,.35)}
.footer-tail{position:absolute;left:853px;top:520px;width:88px;height:9px;background:var(--slate-band)}
.brand-mark{position:absolute;left:37px;top:463px;width:22px;height:22px;border:2.5px solid var(--red);border-radius:50%}
.brand-box{position:absolute;left:0;top:499px;width:88px;height:30px;background:var(--slate-band);color:var(--white);font-family:"Bebas Neue",sans-serif;font-size:12px;line-height:12px;text-align:center;padding-top:4px;letter-spacing:.3px}
.heading{font-family:"Bebas Neue",sans-serif;color:var(--slate);line-height:1}
.heading .accent{color:var(--blue)}
.body-copy{font-size:12px;line-height:21px;color:var(--text)}
.photo{position:absolute}
/* slide 1 */
.welcome-title{position:absolute;left:0;width:941px;top:98px;text-align:center;font-size:38px}
.welcome-photo{left:423px;top:151px;width:94px;height:94px;border-radius:50%;background:radial-gradient(circle at 55% 35%,#8aa0b3,#34495c 55%,#151c24)}
.intro-line{position:absolute;left:0;width:941px;top:282px;text-align:center;font-size:15px;color:var(--red)}
.intro-dot{position:absolute;left:469px;top:308px;width:3px;height:3px;border-radius:50%;background:var(--red)}
.welcome-copy{position:absolute;left:62px;width:817px;top:326px;text-align:center}
/* slide 2 */
.agenda-panel{position:absolute;left:0;top:0;width:204px;height:443px;background:var(--slate-band)}
.agenda-word{position:absolute;left:102px;top:221px;transform:translate(-50%,-50%) rotate(-90deg);font-size:62px;font-weight:300;color:var(--white);letter-spacing:2px;white-space:nowrap}
.agenda-photo{left:204px;top:0;width:286px;height:443px;background:linear-gradient(160deg,#c9d2da 0%,#8d9fb0 40%,#2f4560 75%,#1d2c42 100%)}
.agenda-list{position:absolute;left:490px;top:0;list-style:none}
.agenda-item{position:absolute;left:0;width:370px;height:40px;font-size:24px;font-weight:500;color:var(--slate)}
.agenda-item .pill{position:absolute;left:0;top:2px;width:39px;height:26px;background:var(--red);border-radius:0 14px 14px 0}
.agenda-item .pill svg{position:absolute;left:13px;top:4px;width:18px;height:18px}
.agenda-item .label{position:absolute;left:57px;top:0;line-height:30px}
.agenda-item .rule{position:absolute;left:57px;top:39px;width:313px;height:1px;background:var(--rule)}
/* slide 3 */
.about-title{position:absolute;left:64px;top:72px;font-size:46px}
.about-copy{position:absolute;left:64px;top:121px;width:445px}
.stats-card{position:absolute;left:58px;top:347px;width:484px;height:108px;background:var(--white);border-radius:10px;box-shadow:0 4px 14px rgba(0,0,0,.12)}
.stat{position:absolute;top:18px;width:110px;text-align:center}
.stat svg{width:22px;height:22px}
.stat .value{font-family:"Bebas Neue",sans-serif;font-size:22px;color:var(--slate);line-height:24px;margin-top:6px}
.stat .caption{font-size:10px;color:var(--text)}
.stat-divider{position:absolute;top:28px;width:0;height:54px;border-left:1px dashed var(--blue)}
.stat-badge{position:absolute;left:426px;top:352px;width:92px;height:92px;border-radius:50%;background:var(--slate-band);box-shadow:0 6px 14px rgba(0,0,0,.25);text-align:center;padding-top:18px}
.stat-badge svg{width:24px;height:24px}
.stat-badge .value{font-family:"Bebas Neue",sans-serif;font-size:24px;color:var(--white);line-height:26px}
.about-photo{left:550px;top:97px;width:339px;height:306px;border-radius:14px;background:linear-gradient(170deg,#8d9096 0%,#9a9d9f 28%,#c5332c 45%,#b82a25 80%,#8e201c 100%)}
/* slide 4 */
.product-photo{left:86px;top:84px;width:339px;height:305px;border-radius:12px;background:linear-gradient(90deg,#3a3a3c 0%,#8f9194 10%,#eeeeee 14%,#f4f4f4 86%,#8f9194 90%,#3a3a3c 100%)}
.clients-card{position:absolute;left:225px;top:270px;width:306px;height:169px;background:var(--white);border-radius:14px;box-shadow:0 6px 18px rgba(0,0,0,.14)}
.clients-icon{position:absolute;left:10px;top:21px;width:50px;height:50px;border-radius:50%;background:var(--slate-band);display:flex;align-items:center;justify-content:center}
.clients-icon svg{width:20px;height:20px}
.clients-title{position:absolute;left:73px;top:30px;font-family:"Bebas Neue",sans-serif;font-size:23px;color:var(--blue)}
.clients-copy{position:absolute;left:73px;top:70px;width:215px;font-size:12px;line-height:21px;font-style:italic}
.feature-title{position:absolute;left:462px;top:88px;font-size:46px}
.feature-copy{position:absolute;left:462px;top:143px;width:440px}
.feature-copy-2{position:absolute;left:565px;top:271px;width:340px}
</style>
</head>
<body>

<svg width="0" height="0" style="position:absolute">
  <defs>
    <symbol id="calendar" viewBox="0 0 21 18"><rect x="0" y="1" width="21" height="17" rx="1.5" fill="#e2493b"/><g fill="#fff"><rect x="3" y="6" width="3" height="2"/><rect x="7.5" y="6" width="3" height="2"/><rect x="12" y="6" width="3" height="2"/><rect x="16" y="6" width="2.5" height="2"/><rect x="3" y="10" width="3" height="2"/><rect x="7.5" y="10" width="3" height="2"/><rect x="12" y="10" width="3" height="2"/><rect x="16" y="10" width="2.5" height="2"/><rect x="3" y="14" width="3" height="2"/><rect x="7.5" y="14" width="3" height="2"/><rect x="12" y="14" width="3" height="2"/></g></symbol>
    <symbol id="chevron" viewBox="0 0 18 18"><circle cx="9" cy="9" r="8" fill="none" stroke="#fff" stroke-width="1.3"/><path d="M7.5 5.5 11 9l-3.5 3.5" fill="none" stroke="#fff" stroke-width="1.3"/></symbol>
  </defs>
</svg>

<!-- Welcome -->
<div class="option-title" style="top:69px">Option 1</div>
<section class="slide slate-footer" style="top:153px">
  <div class="date"><svg><use href="#calendar"/></svg>Tuesday , October 26, 2025</div>
  <h2 class="heading welcome-title">WELCOME MESSAGE</h2>
  <div class="photo welcome-photo" role="img" aria-label="Photo of glass office towers viewed from below"></div>
  <p class="intro-line">INTRODUCTION PRESENTATION BOARD MEETING</p>
  <span class="intro-dot"></span>
  <p class="body-copy welcome-copy">Lorem Ipsum is simply dummy text of the printing and typesetting industry. Lorem Ipsum has been the industry's standard dummy text ever since the 1500s, when an unknown printer took a galley of type and scrambled it to make a type specimen book. It has survived not only five centuries, but also the leap into electronic typesetting, remaining essentially unchanged. It was popularised in the 1960s with the release of Letraset sheets containing Lorem Ipsum passages, and more recently with desktop publishing software.</p>
  <span class="brand-mark"></span>
  <div class="footer-band"><span class="copyright">Copyright ©2025 KEYSTONE LANE GAUGING- All Rights Reserved.</span><span class="page-label">Page</span><span class="page-num">5</span></div>
  <div class="brand-box">KEYSTONE LANE<br>GAUGING</div>
  <div class="footer-tail"></div>
</section>

<!-- Agenda -->
<div class="option-title" style="top:696px">Option 2</div>
<section class="slide" style="top:780px">
  <div class="agenda-panel"><span class="agenda-word">AGENDA</span></div>
  <div class="photo agenda-photo" role="img" aria-label="Portrait photo of a businessman in a blue suit with arms crossed"></div>
  <div class="date"><svg><use href="#calendar"/></svg>Tuesday , October 26, 2025</div>
  <ul class="agenda-list">
    <li class="agenda-item" style="top:86px"><span class="pill"><svg><use href="#chevron"/></svg></span><span class="label">Table of content</span><span class="rule"></span></li>
    <li class="agenda-item" style="top:149px"><span class="pill"><svg><use href="#chevron"/></svg></span><span class="label">About Us</span><span class="rule"></span></li>
    <li class="agenda-item" style="top:211px"><span class="pill"><svg><use href="#chevron"/></svg></span><span class="label">Tender Overview</span><span class="rule"></span></li>
    <li class="agenda-item" style="top:274px"><span class="pill"><svg><use href="#chevron"/></svg></span><span class="label">Our Services</span><span class="rule"></span></li>
    <li class="agenda-item" style="top:337px"><span class="pill"><svg><use href="#chevron"/></svg></span><span class="label">Our Team</span><span class="rule"></span></li>
    <li class="agenda-item" style="top:400px"><span class="pill"><svg><use href="#chevron"/></svg></span><span class="label">Contact us</span></li>
  </ul>
  <span class="brand-mark"></span>
  <div class="footer-band"><span class="copyright">Copyright ©2025 KEYSTONE LANE GAUGING- All Rights Reserved.</span><span class="page-label">Page</span><span class="page-num">6</span></div>
  <div class="brand-box">KEYSTONE LANE<br>GAUGING</div>
  <div class="footer-tail"></div>
</section>

<!-- About -->
<div class="option-title" style="top:1323px">Option 3</div>
<section class="slide mixed-footer" style="top:1407px">
  <div class="date"><svg><use href="#calendar"/></svg>Tuesday , October 26, 2025</div>
  <h2 class="heading about-title">ABOUT US</h2>
  <p class="body-copy about-copy">Lorem ipsum dolor sit amet, consectetur adipiscing elit, sed do eiusmod tempor incididunt ut labore et dolore magna aliqua. Ut enim ad minim veniam, quis nostrud exercitation ullamco laboris nisi ut aliquip enim ad minim veniam, quis nostrud exercitation ullamco laboris nisi ut aliquipLorem ipsum dolor sit amet, consectetur adipiscing elit, sed do eiusmod tempor incididunt ut labore et dolore magna aliquants. Ut enim ad minim veniam, quis nostrud exercitation ullamco laboris nisi Lorem ipsum dolor sit amet, consectetur adipiscing elit, sed do eiusmod tempor incididunt ut labore et dolore magna aliqua. Ut enim ad minim veniam, quis nostrud exercitation</p>
  <div class="stats-card">
    <div class="stat" style="left:15px"><svg viewBox="0 0 22 22" fill="none" stroke="#e2493b" stroke-width="1.2"><path d="M11 3a6 6 0 0 0-3.5 10.9V16h7v-2.1A6 6 0 0 0 11 3z"/><path d="M8.5 18h5M9.5 20h3"/></svg><div class="value">9.8M+</div><div class="caption">Edit Your Text</div></div>
    <span class="stat-divider" style="left:125px"></span>
    <div class="stat" style="left:127px"><svg viewBox="0 0 22 22" fill="none" stroke="#e2493b" stroke-width="1.2"><path d="M3 19h16M5 19v-4h3v4M9.5 19v-7h3v7M14 19V9h3v10M4 12l5-4 3 2 6-6"/></svg><div class="value">347K</div><div class="caption">Edit Your Text</div></div>
    <span class="stat-divider" style="left:240px"></span>
    <div class="stat" style="left:242px"><svg viewBox="0 0 22 22" fill="none" stroke="#e2493b" stroke-width="1.2"><rect x="2" y="4" width="18" height="13" rx="1"/><path d="M2 7h18M6 14a5 5 0 0 1 10 0M11 14l2-3"/></svg><div class="value">220K</div><div class="caption">Edit Your Text</div></div>
  </div>
  <div class="stat-badge"><svg viewBox="0 0 24 24" fill="#e2493b"><path d="M6 3h12v5a6 6 0 0 1-12 0zM3 4h3v3a3 3 0 0 1-3-3zm15 0h3a3 3 0 0 1-3 3zM10.5 14h3v4h-3zM8 19h8v2H8z"/></svg><div class="value">250K</div></div>
  <div class="photo about-photo" role="img" aria-label="Photo of a truck driving onto a red steel truck scale deck"></div>
  <span class="brand-mark"></span>
  <div class="footer-band"><span class="copyright">Copyright ©2025 KEYSTONE LANE GAUGING- All Rights Reserved.</span><span class="page-label">Page</span><span class="page-num">7</span></div>
  <div class="brand-box">KEYSTONE LANE<br>GAUGING</div>
  <div class="footer-tail"></div>
</section>

<!-- Feature -->
<div class="option-title" style="top:1950px">Option 4</div>
<section class="slide" style="top:2034px">
  <div class="date"><svg><use href="#calendar"/></svg>Tuesday , October 26, 2025</div>
  <div class="photo product-photo" role="img" aria-label="Photo of stainless steel platform floor scales with digital indicators"></div>
  <div class="clients-card">
    <div class="clients-icon"><svg viewBox="0 0 20 20" fill="#e2493b"><rect x="3" y="12" width="3" height="5"/><rect x="8" y="9" width="3" height="8"/><rect x="13" y="5" width="3" height="12"/></svg></div>
    <h3 class="clients-title">HAPPY CLIENTS</h3>
    <p class="clients-copy">Lorem ipsum dolor sit amet, consectetur adipiscing elit, sed do eiusmod tempor incididunt ut labore et dolore</p>
  </div>
  <h2 class="heading feature-title">HEADING GOES <span class="accent">HERE</span></h2>
  <p class="body-copy feature-copy">Lorem ipsum dolor sit amet, consectetur adipiscing elit, sed do eiusmod tempor incididunt ut labore et dolore magna aliqua. Ut enim ad minim veniam, quis nostrud exercitation ullamco laboris nisi ut aliquip enim ad minim veniam, quis nostrud exercitation ullamco tempor ut aliquip enim ad minim veniam, quis nostrud exercitation ullamco tempor</p>
  <p class="body-copy feature-copy-2">Lorem ipsum dolor sit amet, consectetur adipiscing elit, sed do eiusmod tempor incididunt ut labore et dolore magna aliqua. Ut enim ad minim veniam, quis nostrud exercitation ullamco laboris nisi ut aliquip enim ad minim veniam, quis nostrud exercitation ullamco Lorem ipsum dolor sit amet, consectetur adipiscing elit, sed do eiusmod tempor incididunt ut labore et dolore magna aliqua. Ut enim ad minim veniam,</p>
  <span class="brand-mark"></span>
  <div class="footer-band"><span class="copyright">Copyright ©2025 KEYSTONE LANE GAUGING- All Rights Reserved.</span><span class="page-label">Page</span><span class="page-num">8</span></div>
  <div class="brand-box">KEYSTONE LANE<br>GAUGING</div>
  <div class="footer-tail"></div>
</section>

</body>
</html>
```